New Dental Office Needs an Attractive and user friendly Website Designed

I need a website for a new dental office. The Name is Harrowfield Dentistry. I would like a Modern design with a user friendly interface and usability.
I would like a landing page, a page that lists the services we offer: Cosmetic Dentistry, Implants, Dental Hygiene, Emergency Services, Restorations, Dentures
Target Market(s)
Mid to upper class
Industry/Entity Type
Dentistry
Coding
Number of Pages Required
1 page
Requirements
Must have
- Landing page that has a scheduling option, Procedures, operating hours, and contact us info
Nice to have
- Appealing design, Soft comforting colors. Easy to navigate page, Modern and professional.

```html
<!DOCTYPE html>
<html lang="en">
<head>
<meta charset="utf-8">
<title>Harrowfield Dentistry</title>
<link href="https://fonts.googleapis.com/css2?family=Plus+Jakarta+Sans:wght@400;500;600;700&display=swap" rel="stylesheet">
<style>
:root{
  --stage:#545454;
  --ink:#0f4a5a;
  --teal:#0e5f68;
  --accent:#1a8e9a;
  --mist:#eef4f4;
  --card:#f2f5f5;
  --muted:#6b7c80;
  --line:#d9e3e4;
  --white:#fff;
}
*{box-sizing:border-box;margin:0;padding:0}
html,body{width:747px;height:1200px;overflow:hidden;background:var(--stage)}
body{font-family:"Plus Jakarta Sans",sans-serif;color:var(--ink)}
.board{position:relative;width:1512px;height:2429px;transform:scale(.49405);transform-origin:0 0;overflow:hidden}
.a{position:absolute}
.col{position:absolute;overflow:hidden;background:var(--white)}
.inner{position:relative;width:1512px;height:2429px}
.ph{position:absolute;background:linear-gradient(135deg,#b9cfd3,#e3ecee 60%,#c8d8da)}
.label{font-size:8px;font-weight:500;color:var(--ink);white-space:nowrap}
.h2{font-size:20px;font-weight:600;color:var(--ink);letter-spacing:-.2px;white-space:nowrap}
.p{font-size:7.5px;line-height:13px;color:var(--muted)}
.card{position:absolute;background:var(--card);border-radius:8px}
.stat-t{font-size:12px;color:#555;line-height:16px;font-weight:500;white-space:nowrap}
.stat-n{font-size:24px;font-weight:600;color:var(--ink)}
.btn{position:absolute;border-radius:4px;font-size:7px;font-weight:600;display:flex;align-items:center;justify-content:center;white-space:nowrap}
.nav{display:flex;gap:13px;font-size:7.5px;color:var(--ink);white-space:nowrap}
.svc{position:absolute;left:100px;width:585px;height:58px;border-bottom:1px solid var(--line)}
.svc .num{position:absolute;left:6px;top:26px;font-size:6px;color:var(--ink);transform:rotate(-90deg)}
.svc .name{position:absolute;left:28px;top:20px;font-size:15px;font-weight:600;color:var(--ink);white-space:nowrap}
.svc .desc{position:absolute;left:250px;top:16px;width:200px;font-size:7.5px;line-height:13px;color:#4d5a5e}
.arrow{position:absolute;width:24px;height:24px;border-radius:50%;background:var(--white);color:var(--accent);font-size:12px;display:flex;align-items:center;justify-content:center}
.pg{position:absolute;top:1463px;width:20px;height:20px;border-radius:50%;background:var(--white);font-size:7px;display:flex;align-items:center;justify-content:center}
.member{position:absolute;width:150px;text-align:center}
.member .av{width:68px;height:68px;border-radius:50%;margin:0 auto 8px;background:linear-gradient(135deg,#8fa9b1,#c7d6da)}
.member b{display:block;font-size:8.5px;font-weight:600}
.member i{font-style:normal;font-size:6px;color:var(--accent)}
.faq{position:absolute;left:20px;width:245px;padding-bottom:14px;border-bottom:1px solid var(--line);font-size:9px;font-weight:500;color:var(--ink)}
.faq span{position:absolute;right:0;color:var(--accent);font-size:12px;top:-3px}
.field{position:absolute;height:26px;background:var(--white);border-radius:4px;font-size:7px;color:#aab;padding:8px}
.flabel{position:absolute;font-size:7px;color:var(--ink);white-space:nowrap}
.foot a{display:block;color:var(--white);font-size:7px;margin-bottom:11px;text-decoration:none}
.check{display:flex;gap:8px;font-size:7.5px;color:var(--ink);font-weight:500;margin-bottom:10px;line-height:11px}
.check:before{content:"✓";flex:none;width:9px;height:9px;border-radius:50%;background:var(--ink);color:#fff;font-size:6px;display:flex;align-items:center;justify-content:center}
.why-ic{position:absolute;top:2120px;width:28px;height:28px;border-radius:4px;background:var(--teal)}
.ghost{position:absolute;font-weight:700;color:transparent;-webkit-text-stroke:1px #e6eced;white-space:nowrap}
</style>
</head>
<body>
<div class="board">

<!-- LEFT COLUMN -->
<div class="col" style="left:61px;top:52px;width:663px;height:2377px">
  <div class="inner" style="left:-61px;top:-52px">
    <div class="a" style="left:61px;top:52px;width:663px;height:372px;background:var(--teal)"></div>
    <div class="a" style="left:100px;top:61px;font-size:7px;color:#fff;white-space:nowrap">Mon - Sat : 09:00 AM - 06:00 PM &nbsp;&nbsp;&nbsp; +1 415 555 0192</div>
    <div class="ph" role="img" aria-label="Dentist in a mask treating a patient, teal tinted" style="left:61px;top:79px;width:663px;height:345px;border-radius:14px 14px 0 0;background:linear-gradient(100deg,#2f7f86 0%,#4c9499 45%,#8fbcbf 100%)"></div>
    <div class="a" style="left:86px;top:86px;width:612px;height:38px;background:#fff;border-radius:20px"></div>
    <div class="a" style="left:108px;top:97px;font-size:13px;font-weight:600;color:var(--ink)">Harrowfield</div>
    <div class="a nav" style="left:227px;top:101px"><span>Home</span><span>About us</span><span>Services</span><span>Testimonials</span><span>Case studies</span><span>Gallery</span><span>Blogs</span></div>
    <div class="btn" style="left:580px;top:95px;width:95px;height:20px;background:var(--accent);color:#fff">Book an appointment</div>
    <div class="a" style="left:142px;top:170px;width:280px;font-size:26px;line-height:36px;font-weight:500;color:#fff">Get your confident smile now!</div>
    <div class="a p" style="left:142px;top:244px;width:225px;color:#e6f1f2">Welcome to a place where excellence meets dentistry and patients of all ages experience wide range of personalised dental solutions.</div>
    <div class="btn" style="left:142px;top:310px;width:108px;height:25px;background:#fff;color:var(--ink)">Start using Brightpath</div>
    <div class="a" style="left:61px;top:424px;width:663px;height:74px;background:var(--mist)"></div>
    <div class="a" style="left:100px;top:436px;font-size:30px;font-weight:500;color:var(--ink)">8k+</div>
    <div class="a" style="left:100px;top:477px;font-size:8px;color:var(--ink);white-space:nowrap">Happy Patients</div>
    <div class="a" style="left:178px;top:440px;width:1px;height:44px;background:var(--line)"></div>
    <div class="a p" style="left:192px;top:443px;width:220px;font-size:7px;line-height:12.5px">Let's bring your perfect smile to life! Whether you need a complete smile makeover or routine dental care, we've got you covered.</div>
    <div class="a" style="left:491px;top:360px;width:194px;height:138px;background:var(--teal);border-radius:10px 10px 0 0"></div>
    <div class="a" style="left:510px;top:376px;width:150px;font-size:10px;line-height:15px;font-weight:600;color:#fff">Ready for a Stunning Smile Transformation?</div>
    <div class="a p" style="left:510px;top:413px;width:150px;color:#d5e8ea;font-size:7px;line-height:12.5px">Book an appointment today and let us help you achieve the healthy, beautiful smile you deserve!</div>
    <div class="a" style="left:510px;top:471px;font-size:8px;font-weight:600;color:#fff;white-space:nowrap">Book an Appointment</div>
    <div class="a" style="left:650px;top:468px;width:15px;height:15px;border-radius:50%;background:#fff;color:var(--teal);font-size:9px;text-align:center;line-height:15px">→</div>

    <div class="ph" role="img" aria-label="Dentist with a patient in clinic" style="left:100px;top:560px;width:155px;height:88px;border-radius:44px 44px 0 44px"></div>
    <div class="ph" role="img" aria-label="Smiling dentist in white coat and mask" style="left:215px;top:607px;width:151px;height:224px;border-radius:76px;border:4px solid #fff"></div>
    <div class="a" style="left:272px;top:560px;font-size:24px;font-weight:500;color:var(--ink)">10+</div>
    <div class="a" style="left:322px;top:564px;font-size:7px;line-height:12px;color:var(--ink);white-space:nowrap">Years of<br>Experience</div>
    <div class="ghost" style="left:413px;top:546px;font-size:32px">About Us</div>
    <div class="a label" style="left:415px;top:562px;font-size:7px">About Us</div>
    <div class="a" style="left:413px;top:588px;width:290px;font-size:25px;line-height:32px;font-weight:600;color:var(--ink)">Welcome to Harrowfield Dentistry!</div>
    <div class="a p" style="left:413px;top:662px;width:270px;font-size:7px">We are on a mission to bring smile on people's face since 2011. Harrowfield Dentistry is conveniently located in Los Angeles where we make sure that we provide our patients with best facilities and a seamless dentistry experience.</div>
    <div class="a" style="left:413px;top:731px;width:240px">
      <div class="check">Advanced Technology For Optimal Patient Comfort.</div>
      <div class="check">Happy Patients From Los Angeles, USA, And Around The World</div>
      <div class="check">Expert Teams In Preventive And Curative Dentistry.</div>
      <div class="check">Focus On Aesthetic Value In All Treatments.</div>
    </div>
    <div class="ph" role="img" aria-label="Portrait of the clinic owner" style="left:413px;top:825px;width:28px;height:29px;border-radius:3px"></div>
    <div class="a" style="left:449px;top:827px;font-size:9px;font-weight:500;color:var(--ink);white-space:nowrap">Dr. Nolan Whitaker</div>
    <div class="a" style="left:449px;top:843px;font-size:7px;color:var(--muted);white-space:nowrap">Owner and Director</div>

    <div class="a" style="left:61px;top:897px;width:663px;height:629px;background:var(--mist)"></div>
    <div class="a h2" style="left:61px;top:942px;width:663px;text-align:center">Enjoy Specialized Dental Services</div>
    <div class="svc" style="top:992px"><span class="num">1</span><span class="name">Dental Implants</span><span class="desc">The implant is a medical device made of titanium which serves as the root for missing tooth on top of...</span><span class="arrow" style="left:554px;top:17px">↗</span></div>
    <div class="a" style="left:107px;top:1074px;width:570px;height:71px;background:#fff;border-radius:8px"></div>
    <div class="a" style="left:119px;top:1110px;font-size:6px;transform:rotate(-90deg)">2</div>
    <div class="a" style="left:143px;top:1101px;font-size:15px;font-weight:600;color:var(--accent);white-space:nowrap">Cosmetic Dentistry</div>
    <div class="a" style="left:292px;top:1097px;width:26px;height:26px;border-radius:50%;background:var(--accent);color:#fff;font-size:12px;text-align:center;line-height:26px">↗</div>
    <div class="a" style="left:349px;top:1098px;width:200px;font-size:7.5px;line-height:13px;color:#4d5a5e">The implant is a medical device made of titanium which serves as the root for missing tooth on top of...</div>
    <div class="ph" role="img" aria-label="Dentist examining a smiling patient" style="left:568px;top:1081px;width:97px;height:57px;border-radius:28px"></div>
    <div class="svc" style="top:1170px;border-top:1px solid var(--line)"><span class="num">3</span><span class="name">Dental Hygiene</span><span class="desc">Bleeding gums when brushing is common but not normal and should never be ignored. It may indicate...</span><span class="arrow" style="left:554px;top:17px">↗</span></div>
    <div class="svc" style="top:1240px"><span class="num">4</span><span class="name">Emergency Services</span><span class="desc">Tooth colored resin-based light-cured cement which bonds to the tooth surface. We try and do co...</span><span class="arrow" style="left:554px;top:17px">↗</span></div>
    <div class="svc" style="top:1310px"><span class="num">5</span><span class="name">Restorations</span><span class="desc">Tooth pain is the 2nd most unbearable pain. It can be caused due to many reasons.</span><span class="arrow" style="left:554px;top:17px">↗</span></div>
    <div class="svc" style="top:1380px"><span class="num">6</span><span class="name">Dentures</span><span class="desc">Tooth pain is the 2nd most unbearable pain. It can be caused due to many reasons.</span><span class="arrow" style="left:554px;top:17px">↗</span></div>
    <div class="pg" style="left:323px">←</div>
    <div class="pg" style="left:352px;background:var(--accent);color:#fff">1</div>
    <div class="pg" style="left:382px">2</div>
    <div class="pg" style="left:411px">3</div>
    <div class="pg" style="left:441px">→</div>

    <div class="a label" style="left:100px;top:1571px">See the transformation</div>
    <div class="a h2" style="left:100px;top:1584px">Smile Gallery</div>
    <div class="a p" style="left:466px;top:1572px;width:220px;font-size:7px;line-height:12.5px">The dream of having a perfect smile isn't far-fetched. We'll be happy to contribute in giving you a smile that you love and a smile that you can feel confident in.</div>
    <div class="a" style="left:61px;top:1740px;font-size:36px;font-weight:700;color:#d8ebec;white-space:nowrap;width:155px;overflow:hidden;direction:rtl;text-align:right"><span style="direction:ltr;unicode-bidi:bidi-override">REAL RESU</span></div>
    <div class="a" style="left:568px;top:1740px;font-size:36px;font-weight:700;color:#d8ebec;white-space:nowrap">REAL RESULTS</div>
    <div class="a" style="left:212px;top:1655px;width:360px;height:255px;background:#c9a79a;border-radius:8px"></div>
    <div class="a" style="left:221px;top:1641px;width:343px;height:286px;background:var(--mist);border-radius:8px"></div>
    <div class="ph" role="img" aria-label="Before and after teeth whitening smile" style="left:230px;top:1641px;width:325px;height:222px;border-radius:8px 8px 0 0;background:linear-gradient(90deg,#d6b49a,#e9cbb4 50%,#f0d8c4)"></div>
    <div class="a" style="left:392px;top:1641px;width:2px;height:222px;background:#fff"></div>
    <div class="a" style="left:236px;top:1845px;padding:2px 6px;background:rgba(255,255,255,.7);border-radius:2px;font-size:7px">Before</div>
    <div class="a" style="left:519px;top:1845px;padding:2px 6px;background:rgba(255,255,255,.7);border-radius:2px;font-size:7px">After</div>
    <div class="a" style="left:221px;top:1882px;width:343px;text-align:center;font-size:7.5px;color:var(--accent)">TREATMENTS</div>
    <div class="a" style="left:221px;top:1899px;width:343px;text-align:center;font-size:11px;font-weight:500">Teeth Whitening</div>
    <div class="a" style="left:370px;top:1959px;width:8px;height:3px;border-radius:2px;background:#cfdadb"></div>
    <div class="a" style="left:384px;top:1959px;width:16px;height:3px;border-radius:2px;background:var(--accent)"></div>
    <div class="a" style="left:405px;top:1959px;width:8px;height:3px;border-radius:2px;background:#cfdadb"></div>

    <div class="a" style="left:61px;top:2005px;width:663px;height:242px;background:var(--mist)"></div>
    <div class="a label" style="left:100px;top:2050px">See the difference by yourself</div>
    <div class="a h2" style="left:100px;top:2063px">Why choose us?</div>
    <div class="a p" style="left:466px;top:2051px;width:220px;font-size:7px;line-height:12.5px">We have built an environment of trust and comfort with our patients by using the latest technology and providing best services in cost efficient way.</div>
    <div class="why-ic" style="left:100px"></div><div class="why-ic" style="left:309px"></div><div class="why-ic" style="left:518px"></div>
    <div class="a" style="left:100px;top:2162px;font-size:9px;font-weight:600;white-space:nowrap">High Standard of Dentistry</div>
    <div class="a p" style="left:100px;top:2180px;width:170px;font-size:7px;line-height:12.5px">We provide excellent dentistry experience by using latest technology.</div>
    <div class="a" style="left:309px;top:2162px;font-size:9px;font-weight:600;white-space:nowrap">Committed Dental Team</div>
    <div class="a p" style="left:309px;top:2180px;width:170px;font-size:7px;line-height:12.5px">We are a dedicated team of dentists who are passionate about what they do.</div>
    <div class="a" style="left:518px;top:2162px;font-size:9px;font-weight:600;white-space:nowrap">Modern Equipments</div>
    <div class="a p" style="left:518px;top:2180px;width:170px;font-size:7px;line-height:12.5px">The key to provide better dentistry experience is to evolve with time.</div>

    <div class="a label" style="left:100px;top:2291px">Clinic figures</div>
    <div class="a h2" style="left:100px;top:2304px">Our achievements so far!</div>
    <div class="a p" style="left:466px;top:2292px;width:220px;font-size:7px;line-height:12.5px">We have built an environment of trust and comfort with our patients by using the latest technology and providing best services in cost efficient way.</div>
    <div class="ph" role="img" aria-label="Smiling woman portrait" style="left:100px;top:2361px;width:134px;height:80px;border-radius:8px"></div>
    <div class="card" style="left:250px;top:2361px;width:134px;height:80px"><div class="stat-t a" style="left:15px;top:14px">Brighter Smiles<br>Achieved</div></div>
    <div class="ph" role="img" aria-label="Patient in dental chair" style="left:400px;top:2361px;width:134px;height:80px;border-radius:8px"></div>
    <div class="card" style="left:550px;top:2361px;width:134px;height:80px"><div class="stat-t a" style="left:15px;top:14px">Satisfied Patients<br>and Counting</div></div>
  </div>
</div>

<!-- RIGHT COLUMN -->
<div class="col" style="left:783px;top:0;width:663px;height:2429px">
  <div class="inner" style="left:-783px">
    <div class="a label" style="left:822px;top:40px">Clinic figures</div>
    <div class="a h2" style="left:822px;top:53px">Our achievements so far!</div>
    <div class="a p" style="left:1188px;top:41px;width:220px;font-size:7px;line-height:12.5px">We have built an environment of trust and comfort with our patients by using the latest technology and providing best services in cost efficient way.</div>
    <div class="ph" role="img" aria-label="Smiling woman portrait" style="left:822px;top:110px;width:135px;height:128px;border-radius:8px"></div>
    <div class="card" style="left:972px;top:110px;width:135px;height:128px"><div class="stat-t a" style="left:15px;top:13px">Brighter Smiles<br>Achieved</div><div class="stat-n a" style="left:15px;top:86px">500+</div></div>
    <div class="ph" role="img" aria-label="Young man in dental chair giving thumbs up" style="left:1122px;top:110px;width:135px;height:128px;border-radius:8px"></div>
    <div class="card" style="left:1272px;top:110px;width:135px;height:128px"><div class="stat-t a" style="left:15px;top:13px">Satisfied Patients<br>and Counting</div><div class="stat-n a" style="left:15px;top:86px">8k+</div></div>
    <div class="card" style="left:822px;top:254px;width:135px;height:128px"><div class="stat-t a" style="left:15px;top:13px">Successful Root<br>Canal Treatments</div><div class="stat-n a" style="left:15px;top:86px">2500+</div></div>
    <div class="ph" role="img" aria-label="Dentist treating a patient" style="left:972px;top:254px;width:135px;height:128px;border-radius:8px"></div>
    <div class="card" style="left:1122px;top:254px;width:135px;height:128px"><div class="stat-t a" style="left:15px;top:13px">Successful<br>Implant Surgeries</div><div class="stat-n a" style="left:15px;top:86px">750+</div></div>
    <div class="ph" role="img" aria-label="Dental team with a patient" style="left:1272px;top:254px;width:135px;height:128px;border-radius:8px"></div>

    <div class="a" style="left:783px;top:424px;width:663px;height:427px;background:var(--mist)"></div>
    <div class="member" style="left:818px;top:467px"><div class="av" role="img" aria-label="Team member portrait"></div><b>Dr. Nolan Whitaker</b><i>Owner and director</i></div>
    <div class="member" style="left:960px;top:467px"><div class="av" role="img" aria-label="Team member portrait"></div><b>Mara Ellison</b><i>MDS,Oral &amp; Maxillofacial Surgery</i></div>
    <div class="member" style="left:818px;top:589px"><div class="av" role="img" aria-label="Team member portrait"></div><b>Priya Castell</b><i>MDS,Oral Medicine And Radiology</i></div>
    <div class="member" style="left:960px;top:589px"><div class="av" role="img" aria-label="Team member portrait"></div><b>Owen Hartley</b><i>MDS,Oral &amp; Maxillofacial Surgery</i></div>
    <div class="member" style="left:818px;top:711px"><div class="av" role="img" aria-label="Team member portrait"></div><b>Tessa Brandt</b><i>MDS,Oral Medicine And Radiology</i></div>
    <div class="member" style="left:960px;top:711px"><div class="av" role="img" aria-label="Team member portrait"></div><b>Julian Moreau</b><i>MDS,Oral &amp; Maxillofacial Surgery</i></div>
    <div class="a" style="left:1122px;top:467px;width:285px;height:338px;background:#fff;border-radius:8px">
      <div class="a" style="left:20px;top:18px;font-size:20px;line-height:29px;font-weight:600;white-space:nowrap">Frequently Asked<br>Questions</div>
      <div class="faq" style="top:92px;color:var(--accent)">Will scaling weaken my teeth?<span>−</span>
        <div style="margin-top:10px;font-size:7px;line-height:12.5px;color:var(--muted);font-weight:400">No, Scaling removes calculus and dirt deposited on your tooth making your gums healthy to hold your tooth for a longer time.</div></div>
      <div class="faq" style="top:172px">Are root canal treatment painful?<span>+</span></div>
      <div class="faq" style="top:218px">Are dental implants costly?<span>+</span></div>
      <div class="faq" style="top:264px">Are dental implants costly?<span>+</span></div>
      <div class="faq" style="top:310px;border:0">What if i dont get my missing teeth replaced?<span>+</span></div>
    </div>

    <div class="ph" role="img" aria-label="Smiling patient in dental chair giving thumbs up" style="left:783px;top:893px;width:377px;height:348px;background:linear-gradient(120deg,#d7dfe0,#bfcfd2 50%,#9bb3b7)"></div>
    <div class="a" style="left:1160px;top:893px;width:286px;height:348px;background:var(--teal)"></div>
    <div class="a" style="left:1057px;top:893px;width:300px;height:275px;background:#fff;border-radius:0 0 8px 8px"></div>
    <div class="ghost" style="left:1081px;top:912px;font-size:30px">Testimonials</div>
    <div class="a label" style="left:1083px;top:926px">Testimonials</div>
    <div class="a" style="left:1081px;top:966px;font-size:24px;font-weight:500;white-space:nowrap">Our happy client says</div>
    <div class="ph" role="img" aria-label="Client portrait" style="left:1081px;top:1013px;width:27px;height:27px;border-radius:3px"></div>
    <div class="a" style="left:1117px;top:1013px;font-size:9px;font-weight:500;white-space:nowrap">Henry Calloway</div>
    <div class="a" style="left:1117px;top:1029px;font-size:7px;color:var(--muted);white-space:nowrap">Los Angeles</div>
    <div class="a" style="left:1316px;top:1012px;font-size:28px;font-weight:700;color:var(--accent);line-height:28px">“</div>
    <div class="a p" style="left:1081px;top:1057px;width:252px;font-size:7px;line-height:13px">Cooperative staff, good quality treatment, came from rajkot for dental treatment because of my previous good experience before 4 years. Appointment time were followed with punctuality and no waiting time. The way doctor explain treatment plan was really excellent. Moreover overall treatment cost was economical.</div>
    <div class="a" style="left:1081px;top:1138px;width:18px;height:18px;background:var(--accent);border-radius:3px;color:#fff;font-size:9px;text-align:center;line-height:18px">←</div>
    <div class="a" style="left:1108px;top:1138px;width:18px;height:18px;background:var(--accent);border-radius:3px;color:#fff;font-size:9px;text-align:center;line-height:18px">→</div>

    <div class="ph" role="img" aria-label="Dentist matching tooth shade guide to a patient's smile" style="left:822px;top:1284px;width:285px;height:321px;border-radius:8px;background:linear-gradient(135deg,#c9a79d,#e8cfc6 55%,#d7728f)"></div>
    <div class="a" style="left:1122px;top:1284px;width:285px;height:321px;background:var(--teal);border-radius:8px;padding:20px 23px;color:#fff">
      <div style="font-size:7px">We highly encourage</div>
      <div style="font-size:19px;font-weight:600;margin:3px 0 10px;white-space:nowrap">Lorem Ipsum dummy text</div>
      <p style="font-size:7px;line-height:13px;text-align:justify;color:#e4f0f1;margin-bottom:9px">Lorem Ipsum is simply dummy text of the printing and typesetting industry. There are many variations of passages of Lorem Ipsum available, but the majority have suffered alteration in some form, by injected humour, or randomised words which don't look even slightly believable. If you are going to use a passage of Lorem Ipsum.</p>
      <p style="font-size:7px;line-height:13px;text-align:justify;color:#e4f0f1;margin-bottom:9px">There are many variations of passages of Lorem Ipsum available, but the majority have suffered alteration in some form, by injected humour, or randomised words which don't look even slightly believable. If you are going to use a passage of Lorem Ipsum, you need to be sure there isn't anything embarrassing hidden in the middle of text. There are many variations of passages of Lorem Ipsum available, but the majority have suffered alteration in some form, by injected humour.</p>
      <p style="font-size:7px;line-height:13px;text-align:justify;color:#e4f0f1">There are many variations of passages of Lorem Ipsum available, but the majority have suffered alteration in some form, by injected humour, or randomised words which don't look</p>
    </div>

    <div class="ph" role="img" aria-label="Video of a modern dental treatment room" style="left:783px;top:1648px;width:663px;height:329px;background:linear-gradient(120deg,#7d8a8c,#b9c2c3 45%,#5f6d63)"></div>
    <div class="a" style="left:1079px;top:1799px;width:48px;height:48px;border-radius:50%;background:#fff"></div>
    <svg class="a" style="left:1096px;top:1814px" width="16" height="18" viewBox="0 0 16 18"><path d="M0 0L16 9L0 18Z" fill="#0e5f68"/></svg>
    <div class="a" style="left:822px;top:2018px;width:240px;font-size:20px;line-height:25px;font-weight:500">Schedule Your Appointment Now And Take The First Step</div>
    <div class="a" style="left:1096px;top:1919px;width:311px;height:214px;background:var(--mist);border-radius:8px"></div>
    <div class="a" style="left:1115px;top:1934px;font-size:20px;font-weight:600;white-space:nowrap">Book For Consultation</div>
    <div class="flabel" style="left:1115px;top:1975px">Patient Name</div>
    <div class="flabel" style="left:1257px;top:1975px">Phone Number</div>
    <div class="field" style="left:1115px;top:1989px;width:130px">Enter here</div>
    <div class="field" style="left:1257px;top:1989px;width:130px">Enter here</div>
    <div class="flabel" style="left:1115px;top:2030px">Visit Date/Time</div>
    <div class="flabel" style="left:1257px;top:2030px">Choose Service</div>
    <div class="field" style="left:1115px;top:2044px;width:130px">Select</div>
    <div class="field" style="left:1257px;top:2044px;width:130px">Select<span style="float:right">⌄</span></div>
    <div class="btn" style="left:1115px;top:2087px;width:105px;height:27px;border-radius:14px;background:var(--teal);color:#fff;font-weight:500">Book Appointment</div>

    <div class="a foot" style="left:822px;top:2176px;width:585px;height:228px;background:var(--teal);border-radius:8px;color:#fff">
      <div class="a" style="left:31px;top:22px;font-size:17px;font-weight:600">Harrowfield</div>
      <div class="a" style="left:31px;top:65px;font-size:6.5px;white-space:nowrap">Where amazing smiles begin!</div>
      <div class="a" style="left:166px;top:24px;white-space:nowrap"><div style="font-size:9px;font-weight:600;margin-bottom:16px">Quick link</div><a>About Us</a><a>Services</a><a>Case studies</a><a>Testimonials</a><a>Blogs</a><a>Smile Gallery</a></div>
      <div class="a" style="left:271px;top:24px;width:135px"><div style="font-size:9px;font-weight:600;margin-bottom:16px">Contact us</div>
        <div style="font-size:7px;line-height:12.5px;margin-bottom:8px">418 Linden Grove Ave, Maple Falls, Oregon 97401</div>
        <div style="font-size:7px;margin-bottom:9px">☏ (503) 555-0148</div>
        <div style="font-size:7px;white-space:nowrap">✉ info@harrowfielddentistry.com</div></div>
      <div class="a" style="left:418px;top:24px;white-space:nowrap"><div style="font-size:9px;font-weight:600;margin-bottom:16px">Clinic Timing</div>
        <div style="font-size:7px;margin-bottom:10px">Mon to Sat 9:00 am to 12:30 pm</div>
        <div style="font-size:7px">Mon to Sat 5:00 pm to 8:30 pm</div></div>
      <div class="a" style="left:31px;top:173px;width:523px;height:1px;background:rgba(255,255,255,.25)"></div>
      <div class="a" style="left:31px;top:195px;font-size:7px;white-space:nowrap">Copyright © 2021 Harrowfield Dentistry</div>
      <div class="a" style="left:412px;top:195px;font-size:7px;white-space:nowrap">For emergency cases &nbsp;(503) 555-0148</div>
    </div>
  </div>
</div>

</div>
</body>
</html>
```